Need Help having my business card stand out

I am the owner of Birchway Canine Training and would like for my business cards to stand out. I have been trying to keep designing them myself but I can't get what I have in my head on the card. I will try my best to post templates that I like for inspirations. I want something unique but elegant. I don't want in to look cartoony or cheesy. It needs to pop in a pet shop but also in a coffee shop or gym.

Target Market(s)

Dog owners, Married ,No young kids Jr High school kids and up (maybe kids on the way) Executives, Stay at home moms/wives, Small business owners

Industry/Entity Type

Dog Training

Contact Information for Business Card

Lowell Spratt, 281-904-3376, info@birchwaycanine.example, www.birchwaycanine.example

Colors

Designer to choose colors to be used in the design.

Requirements
Must have
• my logo
Should not have
• Cursive lettering

```html
<!DOCTYPE html>
<html lang="en">
<head>
<meta charset="utf-8">
<title>Birchway Canine Training – Business Card</title>
<link href="https://fonts.googleapis.com/css2?family=Exo+2:wght@400;500;600&display=swap" rel="stylesheet">
<style>
  :root {
    --backdrop: #949494;
    --card-black: #0d0d0d;
    --card-sheen: #1e1e1e;
    --band-grey: #5c5c5c;
    --ink-white: #f4f4f4;
    --photo-warm: #a8875f;
    --photo-dark: #3a3128;
    --photo-plaid: #b84a4f;
    --photo-leaf: #8d9a6a;
  }
  * { box-sizing: border-box; margin: 0; padding: 0; }
  html, body { width: 1200px; height: 941px; overflow: hidden; }
  body {
    background: var(--backdrop);
    font-family: "Exo 2", sans-serif;
    position: relative;
  }
  .card {
    position: absolute;
    background: linear-gradient(160deg, var(--card-sheen), var(--card-black) 55%);
    overflow: hidden;
    box-shadow: 0 6px 18px rgba(0,0,0,.35);
  }
  /* Front */
  .card-front { left: 90px; top: 155px; width: 360px; height: 630px; color: var(--ink-white); }
  .brand {
    position: absolute; top: 90px; left: 0; right: 0; text-align: center;
  }
  .brand-mark {
    width: 54px; height: 54px; border-radius: 50%; border: 3px solid var(--ink-white);
    margin: 0 auto 16px;
  }
  .brand-name {
    font-size: 27px; font-weight: 600; line-height: 1.2; color: var(--ink-white);
  }
  .contact { position: absolute; top: 330px; left: 0; right: 0; text-align: center; }
  .contact-name {
    font-size: 30px; font-weight: 500; letter-spacing: 1px; text-transform: uppercase; margin-bottom: 18px;
  }
  .contact-line { font-size: 19px; font-weight: 400; margin-bottom: 12px; }
  .contact-email { font-size: 17.5px; }
  .web-band {
    position: absolute; left: 0; right: 0; bottom: 0; height: 110px;
    background: var(--band-grey);
    display: flex; align-items: center; justify-content: center;
    font-size: 20px; color: var(--ink-white);
  }
  /* Back */
  .card-back { left: 500px; top: 300px; width: 630px; height: 360px; }
  .photo { position: absolute; top: 0; bottom: 0; }
  .photo-dog {
    left: 0; width: 210px;
    background: linear-gradient(160deg, var(--photo-plaid) 0%, var(--photo-dark) 35%, var(--photo-warm) 60%, var(--photo-dark) 100%);
  }
  .photo-trainer {
    right: 0; width: 230px;
    background: linear-gradient(150deg, var(--photo-leaf) 0%, var(--photo-plaid) 45%, #e3b99a 70%, var(--photo-leaf) 100%);
  }
  .back-band {
    position: absolute; left: 210px; width: 190px; top: 0; bottom: 0;
    background: var(--card-black);
    display: flex; flex-direction: column; align-items: center; justify-content: center; text-align: center;
    color: var(--ink-white); padding: 0 14px;
  }
  .back-band .brand-mark { width: 38px; height: 38px; border-width: 2px; margin-bottom: 12px; }
  .back-band .brand-name { font-size: 19px; }
</style>
</head>
<body>
  <section class="card card-front">
    <div class="brand">
      <div class="brand-mark"></div>
      <p class="brand-name">Birchway Canine<br>Training</p>
    </div>
    <div class="contact">
      <p class="contact-name">Lowell Spratt</p>
      <p class="contact-line">281-904-3376</p>
      <p class="contact-line contact-email">info@birchwaycanine.example</p>
    </div>
    <div class="web-band">www.birchwaycanine.example</div>
  </section>

  <section class="card card-back">
    <div class="photo photo-dog" role="img" aria-label="Photo of a German Shepherd dog with its tongue out beside the trainer's hands in a plaid shirt"></div>
    <div class="back-band">
      <div class="brand-mark"></div>
      <p class="brand-name">Birchway Canine Training</p>
    </div>
    <div class="photo photo-trainer" role="img" aria-label="Portrait photo of the trainer in a red plaid shirt outdoors"></div>
  </section>
</body>
</html>
```